Hi Designers,

I will need 4 web pages designed. The web page looks like an App (if you click on the logo, or the icon on an iPad, it will take you to the website), but it is still a webpage.

Please check the attachment on this brief to understand what specific pages I need to be designed.

A .PSD (straight-up PhotoShop image) as final deliverable is fine, as long as you give us the exact “web color numbers”.

The design is for desktop and iPad but in a single unified web application, NOT separate web app and (native) iPad app.

Details:

Brightwater Policy Partners is developing a browser-based application for use on any mobile device or desktop. The app will be used by corporations to communicate with their employees regarding legal, regulatory and company requirements for conducting business. The app is known as “Harbor Guidance Portal.” When the user clicks on the icon for Harbor Guidance Portal, they will enter a site full of information that a company deems necessary for the employee to do his/her job. There are several content sections within the site, including a login page, training, policies, forms, news feeds and blogs.

The application has been built using Microsoft .NET, and fully supports CSS-type skinning; it uses traditional page layouts. We are seeking a product logo concept (image), a master application/desktop icon (image), as well as a full color scheme/theme/skin design for all areas of the application (header area, body text, menu bar, etc.) in the form of a CSS. The look should be clean, crisp and professional; nothing cartoony or whimsical. It should be easy to read and “airy”.

We have sketched prototypes for the basic application page layout that we can send as a next step of the process.
Updates

Screen shots have been uploaded to this project.  Please use them to guide your design.

Dear designers,

I apologize for the delay in providing feedback. My partners and I will provide feedback in a few days. Thank you for your patience.

Industry/Entity Type

Business

Font styles to use
Other font styles liked:
• see font on screen shots when uploaded

```html
<!DOCTYPE html>
<html lang="en">
<head>
<meta charset="utf-8">
<title>Harbor Guidance Portal — Dashboard</title>
<link href="https://fonts.googleapis.com/css2?family=Fira+Sans:ital,wght@0,400;0,500;0,600;1,400&display=swap" rel="stylesheet">
<style>
  :root {
    --page: #eceef1;
    --panel: #ffffff;
    --topbar: #e6e7e9;
    --line: #d7d9dc;
    --ink: #4a4d52;
    --ink-soft: #7d8186;
    --red: #f0605d;
    --teal: #56d6b5;
    --teal-ink: #2eb893;
    --blue: #4fc3ee;
    --blue-ink: #2fa8da;
    --board-head: #8c8d8f;
    --board-sub: #f4f4f5;
    --row-light: #f7f7f7;
    --row-dark: #d6d7d9;
    --thumb: #9aa7b3;
  }
  * { box-sizing: border-box; margin: 0; padding: 0; }
  html, body { width: 1200px; height: 900px; overflow: hidden; }
  body { background: var(--page); font-family: "Fira Sans", sans-serif; color: var(--ink); font-size: 13px; }

  .app { width: 1200px; height: 900px; display: flex; flex-direction: column; }

  /* top bar */
  .topbar { height: 44px; background: var(--topbar); border-bottom: 1px solid var(--line); display: flex; align-items: center; }
  .nav { display: flex; height: 100%; margin-left: 42px; }
  .nav-item { width: 100px; display: flex; align-items: center; justify-content: center; border-right: 1px dotted #b9bbbf; position: relative; }
  .nav-item svg { width: 24px; height: 24px; fill: none; stroke: #9a9ca0; stroke-width: 1.8; }
  .nav-item.is-active svg { fill: #9a9ca0; stroke: none; }
  .badge { position: absolute; top: 9px; left: 56px; background: var(--red); color: #fff; font-size: 9px; width: 13px; height: 13px; line-height: 13px; text-align: center; border-radius: 2px; }
  .user { margin-left: auto; margin-right: 30px; display: flex; align-items: center; gap: 12px; font-size: 12px; color: var(--ink-soft); }
  .user-avatar { width: 28px; height: 28px; background: linear-gradient(#c9a48c, #7d8fa6); }
  .user .caret { border: 4px solid transparent; border-top-color: #8a8c90; margin-top: 4px; }

  .main { flex: 1; display: flex; min-height: 0; }

  /* news column */
  .news { width: 208px; background: var(--panel); border-right: 1px solid var(--line); }
  .panel-head { height: 28px; display: flex; align-items: center; gap: 8px; padding: 0 12px; font-size: 13px; font-weight: 500; }
  .news .panel-head { background: #b8babd; color: #fff; }
  .panel-head svg { width: 13px; height: 13px; fill: none; stroke: currentColor; stroke-width: 1.8; }
  .search { margin: 10px 12px 6px; height: 24px; border: 1px solid var(--line); display: flex; align-items: center; gap: 6px; padding: 0 8px; font-size: 11px; color: #a3a6aa; }
  .search svg { width: 11px; height: 11px; fill: none; stroke: #a3a6aa; stroke-width: 2; }
  .news-item { display: flex; gap: 10px; padding: 16px 14px 14px 20px; border-bottom: 1px solid #eceef0; position: relative; }
  .news-item.is-current { background: #f3f4f5; }
  .news-item.is-current::before { content: ""; position: absolute; left: 0; top: 0; bottom: 0; width: 4px; background: var(--red); }
  .date { width: 22px; text-align: center; font-size: 8px; color: var(--ink-soft); flex: none; }
  .date svg { width: 22px; height: 22px; fill: none; stroke: #8a8c90; stroke-width: 1.4; }
  .news-body p { font-size: 11px; font-style: italic; line-height: 1.3; }
  .news-body a { display: block; margin-top: 10px; font-size: 11px; color: var(--blue-ink); text-decoration: underline; text-align: right; }

  /* center */
  .center { width: 672px; padding: 12px 12px 0 12px; display: flex; flex-direction: column; gap: 10px; }
  .welcome { background: var(--panel); }
  .welcome .panel-head { background: var(--red); color: #fff; }
  .welcome .panel-head svg { fill: #fff; stroke: none; }
  .welcome-body { display: flex; gap: 16px; padding: 10px 14px 14px; }
  .welcome-photo { width: 58px; height: 52px; flex: none; background: linear-gradient(135deg, #e9d39a, #9a8a7a); }
  .welcome-body p { font-size: 11px; font-style: italic; line-height: 1.35; }

  .columns { flex: 1; display: flex; gap: 10px; min-height: 0; }
  .whats-new { width: 330px; background: var(--panel); }
  .whats-new .panel-head { background: var(--teal); color: #fff; }
  .update { display: flex; gap: 12px; padding: 14px 16px 12px; border-bottom: 1px solid #eceef0; }
  .update:nth-child(even) { padding-left: 34px; }
  .update-thumb { width: 34px; height: 30px; flex: none; background: linear-gradient(#d7dde3, var(--thumb)); }
  .update h3 { font-size: 12px; font-weight: 500; color: var(--teal-ink); }
  .update p { font-size: 11px; font-style: italic; line-height: 1.3; margin-top: 2px; }

  .game { flex: 1; background: #f0f1f3; }
  .game .panel-head { background: var(--blue); color: #fff; }
  .game .panel-head svg { fill: #fff; stroke: none; }
  .game-card { background: var(--panel); margin: 8px 10px 0; padding: 14px 14px 16px; border-bottom: 3px solid #c8cacd; display: flex; gap: 14px; height: 112px; }
  .game-card svg { width: 26px; height: 26px; flex: none; fill: none; stroke: var(--blue); stroke-width: 1.8; margin-top: 4px; }
  .game-card h3 { font-size: 15px; font-weight: 400; margin: 4px 0 8px; }
  .game-card p { font-size: 11px; font-style: italic; line-height: 1.35; }

  /* leaderboard */
  .board { flex: 1; background: var(--row-light); border-left: 1px solid var(--line); }
  .board .panel-head { background: var(--board-head); color: #fff; justify-content: flex-start; padding-left: 22px; }
  .board-table { width: 100%; border-collapse: collapse; font-size: 12px; }
  .board-table th { background: var(--board-sub); font-weight: 400; font-size: 10px; color: var(--ink-soft); height: 26px; text-align: left; }
  .board-table td { height: 29.6px; }
  .board-table tr:nth-child(even) td { background: var(--row-dark); }
  .board-table .rank { width: 46px; text-align: center; font-size: 9px; }
  .board-table .pct { width: 66px; }
  .board-table .score { width: 68px; }
</style>
</head>
<body>
<div class="app">
  <header class="topbar">
    <nav class="nav">
      <div class="nav-item is-active"><svg viewBox="0 0 24 24"><path d="M12 3a6 6 0 0 1 6 6v5l2 3H4l2-3V9a6 6 0 0 1 6-6zm-2 16h4a2 2 0 0 1-4 0z"/></svg><span class="badge">2</span></div>
      <div class="nav-item"><svg viewBox="0 0 24 24"><rect x="4" y="4" width="16" height="16"/><path d="M7 9h10M7 13h10M7 17h6"/></svg></div>
      <div class="nav-item"><svg viewBox="0 0 24 24"><rect x="3" y="5" width="18" height="11"/><path d="M9 20h6M12 16v4"/></svg></div>
      <div class="nav-item"><svg viewBox="0 0 24 24"><path d="M19 11a7 7 0 0 0-12-4l-2 2M5 13a7 7 0 0 0 12 4l2-2"/><path d="M5 5v4h4M19 19v-4h-4"/></svg></div>
    </nav>
    <div class="user">
      <div class="user-avatar" role="img" aria-label="User profile photo"></div>
      <span>Daniel Hartley</span>
      <span class="caret"></span>
    </div>
  </header>

  <div class="main">
    <aside class="news">
      <div class="panel-head"><svg viewBox="0 0 14 14"><path d="M2 12l1-3 7-7 2 2-7 7z"/></svg>Industry news</div>
      <div class="search"><svg viewBox="0 0 12 12"><circle cx="5" cy="5" r="3.5"/><path d="M8 8l3 3"/></svg>Search news...</div>

      <div class="news-item">
        <div class="date"><svg viewBox="0 0 22 22"><rect x="2" y="3" width="18" height="17"/><path d="M2 8h18"/><text x="11" y="17" font-size="7" text-anchor="middle" fill="#8a8c90" stroke="none">29</text></svg>oct</div>
        <div class="news-body"><p>Lorem ipsum dolor sit amet, ad his meis vocibus. An nam possim lorem ipsum dolor</p><a>monthly report/major's office</a></div>
      </div>
      <div class="news-item is-current">
        <div class="date"><svg viewBox="0 0 22 22"><rect x="2" y="3" width="18" height="17"/><path d="M2 8h18"/><text x="11" y="17" font-size="7" text-anchor="middle" fill="#8a8c90" stroke="none">29</text></svg>oct</div>
        <div class="news-body"><p>Lorem ipsum dolor sit amet, ad his meis vocibus. An nam possim fastidii, usu in fuisset dissentias, nec at persius denique.</p><a>monthly report/major's office</a></div>
      </div>
      <div class="news-item">
        <div class="date"><svg viewBox="0 0 22 22"><rect x="2" y="3" width="18" height="17"/><path d="M2 8h18"/><text x="11" y="17" font-size="7" text-anchor="middle" fill="#8a8c90" stroke="none">29</text></svg>oct</div>
        <div class="news-body"><p>Lorem ipsum dolor sit amet, ad his meis vocibus. An nam possim fastidii, usu in fuisset dissentias, nec at persius denique.</p><a>monthly report/major's office</a></div>
      </div>
      <div class="news-item">
        <div class="date"><svg viewBox="0 0 22 22"><rect x="2" y="3" width="18" height="17"/><path d="M2 8h18"/><text x="11" y="17" font-size="7" text-anchor="middle" fill="#8a8c90" stroke="none">29</text></svg>oct</div>
        <div class="news-body"><p>Lorem ipsum dolor sit amet, ad his meis vocibus. An nam possim fastidii, usu in fuisset dissentias, nec at persius denique.</p><a>monthly report/major's office</a></div>
      </div>
    </aside>

    <section class="center">
      <div class="welcome">
        <div class="panel-head"><svg viewBox="0 0 14 14"><path d="M7 1l1.8 3.9 4.2.4-3.2 2.8 1 4.1L7 10 3.2 12.2l1-4.1L1 5.3l4.2-.4z"/></svg>Welcome to Harbor Guidance Portal</div>
        <div class="welcome-body">
          <div class="welcome-photo" role="img" aria-label="Portrait photo of the portal host"></div>
          <p>Lorem ipsum dolor sit amet, mundi cotidie gloriatur no vim, mea fabulas sensibus ad. Ut possit pericula nec, per te ullum omnes, intellegat an vis. Eos te dico verear lobortis, facilisi definitionem te mei, ei vel doming.</p>
        </div>
      </div>

      <div class="columns">
        <div class="whats-new">
          <div class="panel-head"><svg viewBox="0 0 14 14"><path d="M2 2h10v7H6l-3 3V9H2z" fill="#fff" stroke="none"/></svg>What's new</div>
          <div class="update-list">
            <article class="update"><div class="update-thumb" role="img" aria-label="News thumbnail photo"></div><div><h3>11/11/2013</h3><p>Prompta cibus gloriatur mea te, an cum facete suavitate, ei vim corrumpit</p></div></article>
            <article class="update"><div class="update-thumb" role="img" aria-label="News thumbnail photo"></div><div><h3>11/11/2013</h3><p>Prompta cibus gloriatur mea te, an cum facete suavitate, ei vim corrumpit</p></div></article>
            <article class="update"><div class="update-thumb" role="img" aria-label="News thumbnail photo"></div><div><h3>11/11/2013</h3><p>Prompta cibus gloriatur mea te, an cum facete suavitate, ei vim corrumpit</p></div></article>
            <article class="update"><div class="update-thumb" role="img" aria-label="News thumbnail photo"></div><div><h3>11/11/2013</h3><p>Prompta cibus gloriatur mea te, an cum facete suavitate, ei vim corrumpit</p></div></article>
            <article class="update"><div class="update-thumb" role="img" aria-label="News thumbnail photo"></div><div><h3>11/11/2013</h3><p>Prompta cibus gloriatur mea te, an cum facete suavitate, ei vim corrumpit</p></div></article>
            <article class="update"><div class="update-thumb" role="img" aria-label="News thumbnail photo"></div><div><h3>11/11/2013</h3><p>Prompta cibus gloriatur mea te, an cum facete suavitate, ei vim corrumpit</p></div></article>
          </div>
        </div>

        <div class="game">
          <div class="panel-head"><svg viewBox="0 0 14 14"><circle cx="7" cy="4.5" r="2.8"/><path d="M1.5 13a5.5 5 0 0 1 11 0z"/></svg>Compliance game center</div>
          <article class="game-card"><svg viewBox="0 0 26 26"><circle cx="13" cy="10" r="5"/><path d="M4 23a9 8 0 0 1 18 0"/></svg><div><h3>Use Preferances</h3><p>Lorem ipsum dolor sit amet, ad his meis vocibus. An nam possim fastidii, usu in fuisset dissentias,</p></div></article>
          <article class="game-card"><svg viewBox="0 0 26 26"><path d="M3 4h20v13H11l-6 5v-5H3z"/><path d="M8 9h10M8 13h6"/></svg><div><h3>Real Time Updates</h3><p>Lorem ipsum dolor sit amet, ad his meis vocibus. An nam possim fastidii, usu in fuisset dissentias,</p></div></article>
          <article class="game-card"><svg viewBox="0 0 26 26"><rect x="3" y="3" width="20" height="20"/><path d="M7 8h2M12 8h7M7 13h2M12 13h7M7 18h2M12 18h7"/></svg><div><h3>Team Standings</h3><p>Lorem ipsum dolor sit amet, ad his meis vocibus. An nam possim fastidii, usu in fuisset dissentias,</p></div></article>
          <article class="game-card"><svg viewBox="0 0 26 26"><path d="M13 4a6 6 0 0 1 4 10.5V18H9v-3.5A6 6 0 0 1 13 4zM10 21h6"/><path d="M3 10h2M21 10h2M6 3l1.5 1.5M20 3l-1.5 1.5"/></svg><div><h3>Earn Bonus Points</h3><p>Lorem ipsum dolor sit amet, ad his meis vocibus. An nam possim fastidii, usu in fuisset dissentias,</p></div></article>
        </div>
      </div>
    </section>

    <aside class="board">
      <div class="panel-head">Leaderboard</div>
      <table class="board-table">
        <tr><th class="rank">rank</th><th>player</th><th class="pct">%</th><th class="score">score</th></tr>
        <tr><td class="rank">1</td><td>Micheal, L</td><td class="pct">92%</td><td class="score">5093</td></tr>
        <tr><td class="rank">2</td><td>Angella,D</td><td class="pct">91%</td><td class="score">5029</td></tr>
        <tr><td class="rank">3</td><td>Micheal, L</td><td class="pct">92%</td><td class="score">5093</td></tr>
        <tr><td class="rank">2</td><td>Angella,D</td><td class="pct">91%</td><td class="score">5029</td></tr>
        <tr><td class="rank">3</td><td>Micheal, L</td><td class="pct">92%</td><td class="score">5093</td></tr>
        <tr><td class="rank">3</td><td>Micheal, L</td><td class="pct">92%</td><td class="score">5093</td></tr>
        <tr><td class="rank">3</td><td>Micheal, L</td><td class="pct">92%</td><td class="score">5093</td></tr>
        <tr><td class="rank">2</td><td>Angella,D</td><td class="pct">91%</td><td class="score">5029</td></tr>
        <tr><td class="rank">3</td><td>Micheal, L</td><td class="pct">92%</td><td class="score">5093</td></tr>
        <tr><td class="rank">3</td><td>Micheal, L</td><td class="pct">92%</td><td class="score">5093</td></tr>
        <tr><td class="rank">2</td><td>Angella,D</td><td class="pct">91%</td><td class="score">5029</td></tr>
        <tr><td class="rank">2</td><td>Angella,D</td><td class="pct">91%</td><td class="score">5029</td></tr>
        <tr><td class="rank">3</td><td>Micheal, L</td><td class="pct">92%</td><td class="score">5093</td></tr>
        <tr><td class="rank">2</td><td>Angella,D</td><td class="pct">91%</td><td class="score">5029</td></tr>
        <tr><td class="rank">3</td><td>Micheal, L</td><td class="pct">92%</td><td class="score">5093</td></tr>
        <tr><td class="rank">3</td><td>Micheal, L</td><td class="pct">92%</td><td class="score">5093</td></tr>
        <tr><td class="rank">2</td><td>Angella,D</td><td class="pct">91%</td><td class="score">5029</td></tr>
        <tr><td class="rank">3</td><td>Micheal, L</td><td class="pct">92%</td><td class="score">5093</td></tr>
        <tr><td class="rank">2</td><td>Angella,D</td><td class="pct">91%</td><td class="score">5029</td></tr>
        <tr><td class="rank">3</td><td>Micheal, L</td><td class="pct">92%</td><td class="score">5093</td></tr>
        <tr><td class="rank">3</td><td>Micheal, L</td><td class="pct">92%</td><td class="score">5093</td></tr>
        <tr><td class="rank">2</td><td>Angella,D</td><td class="pct">91%</td><td class="score">5029</td></tr>
        <tr><td class="rank">3</td><td>Micheal, L</td><td class="pct">92%</td><td class="score">5093</td></tr>
        <tr><td class="rank">3</td><td>Micheal, L</td><td class="pct">92%</td><td class="score">5093</td></tr>
        <tr><td class="rank">2</td><td>Angella,D</td><td class="pct">91%</td><td class="score">5029</td></tr>
        <tr><td class="rank">3</td><td>Micheal, L</td><td class="pct">92%</td><td class="score">5093</td></tr>
      </table>
    </aside>
  </div>
</div>
</body>
</html>
```